Powerpoint Design for AI Consulting Company

Description
Velmora Quill Industries is a consulting and technology company that engineers AI transformations, automation, and decision intelligence for financial firms, mining companies, and supply chains.
We already have a logo and brand colors (see attached). We need a professional, modern PowerPoint template that reflects our brand identity and positioning.
Key Requirements
Use our logo and color palette (deep blue, orange, white/black backgrounds).
Clean, modern design with subtle technology-inspired elements (data flows, AI networks, abstract systems).
Must feel sophisticated, bold, and boardroom-ready for executive presentations.
Templates should support both dark and light backgrounds.
Deliverables
A reusable PowerPoint template (.PPTX) with at least these layouts:
Title / Cover slide – dramatic, logo placement, tagline space.
Agenda slide – clean, structured layout.
Section divider slides – strong use of brand colors.
Content slides – text + image, text + icon.
Charts & data slides – bar, line, pie, comparison table, infographics.
Case study / example project slide. - ROI / Transformation Journey
Timeline / roadmap slide.
Team profile slide.
Reframe Slide – A provocative insight that reframes the client’s current thinking.
Options & Trade-offs Slide – Matrix showing different paths and consequences.
Execution Roadmap Slide – Step-by-step phased implementation view.
Closing / thank-you slide with contact details.
Style Guide
Colors: Primary – deep blue (#0D3559), Secondary – orange (#E87722), Accents – silver/white.
Fonts: Modern sans-serif (e.g., Montserrat, Lato, or similar).
Visual elements: Abstract technology, data-inspired graphics, mathematical motifs. Avoid clutter or overly “sci-fi” looks.
Tone: Premium consulting + innovative AI firm.
Target Market(s)
Velmora Quill Industries’ target market is senior decision-makers in finance, mining, and supply chains, where complexity, risk, and ROI pressure are high. Primary buyers include family offices, boutique wealth managers, super funds, and mining/supply chain executives, who value insight-driven strategies, automation, and decision intelligence. A secondary market includes professional services (accounting, legal, medical) and regulated SMEs (daycare, aged care, community services) burdened by admin and compliance. The slide deck must appeal to a boardroom audience — authoritative, data-driven, and visually clean — while remaining flexible enough to adapt for SME professional services.
Look and feel
Each slider illustrates characteristics of the customer's brand and the style your logo design should communicate.

```html
<!DOCTYPE html>
<html lang="en">
<head>
<meta charset="utf-8">
<title>Velmora Quill Industries – Presentation Template</title>
<link rel="stylesheet" href="https://fonts.googleapis.com/css2?family=Lato:wght@400;700;900&display=swap">
<style>
:root{
  --stage:#8a8a8a;
  --navy:#0f2a4f;
  --navy-deep:#071a33;
  --navy-mid:#143a68;
  --orange:#e0601a;
  --orange-soft:#c45a1e;
  --white:#ffffff;
  --silver:#cdd6e2;
}
*{margin:0;padding:0;box-sizing:border-box}
html,body{width:996px;height:1200px;overflow:hidden;background:var(--stage);font-family:'Lato',sans-serif;color:var(--white)}
.canvas{position:relative;width:996px;height:1200px}
.slide{position:absolute;width:431px;height:242px;overflow:hidden;background:linear-gradient(160deg,var(--navy-mid) 0%,var(--navy) 55%,var(--navy-deep) 100%);box-shadow:0 6px 16px rgba(0,0,0,.35)}
.col-a{left:57px}.col-b{left:508px}
.row-1{top:87px}.row-2{top:348px}.row-3{top:609px}.row-4{top:870px}
.abs{position:absolute}
.slide-title{position:absolute;left:16px;top:26px;padding-left:8px;border-left:1.5px solid var(--orange);font-weight:700;font-size:18px;line-height:20px;letter-spacing:.2px;text-transform:uppercase}
.accent{color:var(--orange)}
.brand{position:absolute;right:12px;top:16px;width:70px;text-align:center;font-weight:700;font-size:8.5px;line-height:9.5px;color:var(--white);letter-spacing:.3px}
.brand-dot{display:block;width:9px;height:9px;border-radius:50%;background:var(--white);margin:0 auto 3px}
.footer{position:absolute;left:0;bottom:0;width:431px;height:22px}
.footer-text{position:absolute;left:52px;bottom:4px;font-size:5px;color:var(--silver);display:flex;align-items:center;gap:4px}
.ico{display:inline-block;width:5px;height:5px;background:var(--orange);border-radius:1px}
.socials{position:absolute;left:360px;bottom:3px;display:flex;gap:3px}
.socials span{width:9px;height:9px;border-radius:50%;border:.8px solid var(--white)}
.socials span:first-child{background:var(--white)}
.page-no{position:absolute;left:415px;bottom:4px;width:9px;height:9px;border-radius:50%;background:var(--orange);font-size:4px;line-height:9px;text-align:center;font-weight:700}
.body-text{font-size:6.2px;line-height:12.5px;color:var(--silver);text-align:justify}
/* cover */
.cover{background:linear-gradient(180deg,#061630 0%,#0c2140 45%,#2a2a33 72%,#7a3f18 100%)}
.cover-brand{position:absolute;left:44px;top:88px;width:124px;text-align:center;font-weight:700;font-size:12px;line-height:14px;letter-spacing:.4px}
.cover-brand .brand-dot{width:16px;height:16px;margin-bottom:6px}
.cover-title{position:absolute;left:208px;top:32px;font-weight:700;font-size:23px;line-height:29px;text-transform:uppercase}
.cover-tag{position:absolute;left:208px;top:97px;font-size:12.5px}
/* chart */
.bullets{position:absolute;left:26px;top:66px;width:168px;list-style:none}
.bullets li{position:relative;padding-left:13px;margin-bottom:4px;font-size:6.2px;line-height:12.5px;color:var(--silver);text-align:justify}
.bullets li::before{content:"";position:absolute;left:0;top:4.5px;width:3.5px;height:3.5px;border-radius:50%;background:var(--orange)}
.chart{position:absolute;left:215px;top:55px;width:205px;height:150px}
/* agenda */
.agenda-list{position:absolute;left:25px;top:71px;list-style:none}
.agenda-list li{display:flex;align-items:center;height:16.5px;font-size:7.4px}
.num{width:9px;height:9px;border-radius:50%;background:var(--orange);font-size:3.6px;line-height:9px;text-align:center;font-weight:700;margin-right:13px}
.globe-ring{position:absolute;left:186px;top:32px;width:177px;height:177px;border-radius:50%;border:1px solid rgba(120,160,210,.45)}
.globe{position:absolute;left:193px;top:39px;width:163px;height:163px;border-radius:50%;background:radial-gradient(circle at 50% 30%,#3fa2f0 0%,#125aa8 35%,#0a2550 70%,#081a38 100%)}
/* case study */
.case-image{position:absolute;left:19px;top:65px;width:134px;height:134px;border-radius:50%;background:radial-gradient(circle at 55% 40%,#7d6fb8 0%,#2f64b5 35%,#17305d 70%,#05101f 100%)}
.timeline-line{position:absolute;left:183.5px;top:55px;width:1px;height:136px;background:var(--white)}
.step-icon{position:absolute;left:168px;width:32px;height:32px;border-radius:50%;background:var(--orange)}
.step{position:absolute;left:212px;width:124px}
.step h3{font-size:9px;font-weight:700;margin-bottom:6px}
.step p{font-size:5.6px;line-height:8.8px;color:var(--silver);text-align:justify}
/* about */
.about-text{position:absolute;left:24px;top:66px;width:166px}
.about-art{position:absolute;left:180px;top:54px;width:245px;height:170px;background:radial-gradient(ellipse at 70% 55%,rgba(60,120,200,.55) 0%,rgba(20,60,120,.25) 50%,rgba(15,42,79,0) 75%)}
.node{position:absolute;width:32px;height:32px;border-radius:50%;background:var(--orange)}
.node-label{position:absolute;font-size:6px;line-height:8px;font-weight:700;text-align:center;width:50px}
/* team */
.member{position:absolute;top:64px;width:96px;text-align:center}
.portrait{width:83px;height:83px;margin:0 auto;border-radius:50%;border:1.5px solid var(--orange);background:linear-gradient(180deg,#8391a5 0%,#4f5d73 55%,#2c3445 100%)}
.member h4{font-size:9px;font-weight:700;margin-top:5px}
.member p{font-size:5.6px;line-height:8.8px;color:var(--silver);margin-top:6px}
/* divider */
.divider{background:linear-gradient(180deg,#060c18 0%,#0b1a30 50%,#3a2a22 80%,#9a4a18 100%)}
.divider-art{position:absolute;left:60px;top:0;width:260px;height:242px;background:radial-gradient(circle at 50% 55%,rgba(140,180,230,.45) 0%,rgba(40,80,140,.25) 35%,rgba(10,20,40,0) 70%)}
.divider-band{position:absolute;left:224px;top:147px;width:210px;height:43px;border-radius:22px 0 0 22px;background:var(--navy);border-left:2px solid var(--orange);border-top:1px solid var(--orange);border-bottom:1px solid var(--orange)}
.divider-title{position:absolute;left:251px;top:157px;font-size:18px;font-weight:700;letter-spacing:.2px}
/* thanks */
.thanks{background:linear-gradient(180deg,#10305a 0%,#0f2a4f 55%,#3b3431 85%,#6e3c1c 100%)}
.thanks .slide-title{top:22px;font-size:27.5px;line-height:30px;border-left-width:2px}
.thanks-art{position:absolute;left:0;top:50px;width:340px;height:192px;background:radial-gradient(ellipse at 60% 40%,rgba(60,110,210,.55) 0%,rgba(30,60,120,.3) 45%,rgba(15,42,79,0) 75%)}
.contact{position:absolute;left:317px;top:138px}
.contact h5{font-size:8px;font-weight:700;margin-bottom:10px}
.contact p{font-size:7.4px;margin-bottom:8px;display:flex;align-items:center;gap:5px}
.contact .ico{width:6px;height:6px}
.contact .socials{position:static;margin-top:8px;gap:4px}
.contact .socials span{width:14px;height:14px;border-width:1px}
</style>
</head>
<body>
<div class="canvas">

  <!-- Cover -->
  <section class="slide cover col-a row-1">
    <div class="cover-brand"><span class="brand-dot"></span>VELMORA QUILL<br>INDUSTRIES</div>
    <h1 class="cover-title">Velmora Quill<br><span class="accent">Industries</span></h1>
    <p class="cover-tag">AI Consulting &amp; Transformation</p>
  </section>

  <!-- Chart -->
  <section class="slide col-b row-1">
    <h2 class="slide-title">Chart <span class="accent">Title</span></h2>
    <div class="brand"><span class="brand-dot"></span>VELMORA QUILL INDUSTRIES</div>
    <ul class="bullets">
      <li>Sed ut perspiciatis unde omnis iste natus error sit voluptatem accusantium doloremque laudantium, totam rem aperiam, eaque ipsa quae ab illo inventore veritatis et quasi architecto beatae vitae dicta sunt explicabo.</li>
      <li>Nemo enim ipsam voluptatem quia voluptas sit aspernatur aut odit aut fugit, sed quia consequuntur magni dolores eos qui ratione voluptatem sequi nesciunt. Neque porro quisquam est, qui dolorem ipsum</li>
      <li>Quia dolor sit amet, consectetur, adipisci velit, sed quia non numquam eius modi tempora incidunt ut labore et dolore magnam aliquam quaerat voluptatem.</li>
    </ul>
    <svg class="chart" viewBox="0 0 205 150" font-family="Lato, sans-serif" fill="#fff">
      <circle cx="52" cy="6" r="2" fill="#e0601a"/><text x="57" y="8" font-size="4">Lorem</text>
      <circle cx="80" cy="6" r="2" fill="#fff"/><text x="85" y="8" font-size="4">Ipsum</text>
      <g font-size="5.5" text-anchor="end">
        <text x="12" y="29">50</text><text x="12" y="51">40</text><text x="12" y="74">30</text>
        <text x="12" y="96">20</text><text x="12" y="119">10</text><text x="12" y="141">0</text>
      </g>
      <path d="M20 10 V142 H197" stroke="rgba(255,255,255,.35)" stroke-width=".6" fill="none"/>
      <g stroke-width="2.6" stroke-linecap="round">
        <line x1="33" y1="32" x2="33" y2="137" stroke="#e0601a"/><line x1="41" y1="75" x2="41" y2="137" stroke="#fff"/>
        <line x1="52" y1="32" x2="52" y2="137" stroke="#fff"/><line x1="60" y1="75" x2="60" y2="137" stroke="#e0601a"/>
        <line x1="71" y1="32" x2="71" y2="137" stroke="#e0601a"/><line x1="79" y1="75" x2="79" y2="137" stroke="#e0601a"/>
        <line x1="90" y1="32" x2="90" y2="137" stroke="#fff"/><line x1="98" y1="75" x2="98" y2="137" stroke="#e0601a"/>
        <line x1="109" y1="32" x2="109" y2="137" stroke="#fff"/><line x1="117" y1="75" x2="117" y2="137" stroke="#e0601a"/>
        <line x1="128" y1="32" x2="128" y2="137" stroke="#e0601a"/><line x1="136" y1="75" x2="136" y2="137" stroke="#fff"/>
        <line x1="147" y1="32" x2="147" y2="137" stroke="#e0601a"/><line x1="155" y1="75" x2="155" y2="137" stroke="#fff"/>
        <line x1="166" y1="32" x2="166" y2="137" stroke="#e0601a"/><line x1="174" y1="75" x2="174" y2="137" stroke="#fff"/>
      </g>
      <g font-size="5" text-anchor="middle">
        <text x="37" y="151">JAN</text><text x="56" y="151">FEB</text><text x="75" y="151">MAR</text><text x="94" y="151">APR</text>
        <text x="113" y="151">MAY</text><text x="132" y="151">JUN</text><text x="151" y="151">JUL</text><text x="170" y="151">AUG</text>
      </g>
    </svg>
    <svg class="footer" viewBox="0 0 431 22" fill="none" stroke="#fff" stroke-width=".8"><path d="M25 22 C25 10 31 2 45 2 H395 C404 2 406 10 409 22"/><path d="M404 22 C412 20 414 0 419 0 C424 0 425 20 431 22"/></svg>
    <div class="footer-text"><span class="ico"></span>Call Us : +1 555 014 2290 &nbsp;| &nbsp;<span class="ico"></span>info@velmoraquill.com</div>
    <div class="socials"><span></span><span></span><span></span></div>
    <div class="page-no">05</div>
  </section>

  <!-- Agenda -->
  <section class="slide col-a row-2">
    <h2 class="slide-title">Our <span class="accent">Agenda</span></h2>
    <div class="brand"><span class="brand-dot"></span>VELMORA QUILL INDUSTRIES</div>
    <ol class="agenda-list">
      <li><span class="num">01</span>Sed ut perspiciatis unde omnis</li>
      <li><span class="num">02</span>Iiste natus error sit voluptatem</li>
      <li><span class="num">03</span>Accusantium doloremque</li>
      <li><span class="num">04</span>Laudantiumtotam rem aperiam</li>
      <li><span class="num">06</span>Eeaque ipsa quaeim ipsam</li>
      <li><span class="num">07</span>Sed ut perspiciatis unde omnis</li>
      <li><span class="num">08</span>Iiste natus error sit voluptatem</li>
      <li><span class="num">09</span>Accusantium doloremque</li>
    </ol>
    <div class="globe-ring"></div>
    <div class="globe" role="img" aria-label="Photograph of Earth from orbit with a blue sunrise glow"></div>
    <svg class="footer" viewBox="0 0 431 22" fill="none" stroke="#fff" stroke-width=".8"><path d="M25 22 C25 10 31 2 45 2 H395 C404 2 406 10 409 22"/><path d="M404 22 C412 20 414 0 419 0 C424 0 425 20 431 22"/></svg>
    <div class="footer-text"><span class="ico"></span>Call Us : +1 555 014 2290 &nbsp;| &nbsp;<span class="ico"></span>info@velmoraquill.com</div>
    <div class="socials"><span></span><span></span><span></span></div>
    <div class="page-no">02</div>
  </section>

  <!-- Case study -->
  <section class="slide col-b row-2">
    <h2 class="slide-title">Case <span class="accent">Study</span></h2>
    <div class="brand"><span class="brand-dot"></span>VELMORA QUILL INDUSTRIES</div>
    <div class="case-image" role="img" aria-label="Illustration of an AI head surrounded by glowing data streams"></div>
    <div class="timeline-line"></div>
    <div class="step-icon" style="top:39px"></div>
    <div class="step-icon" style="top:107px"><svg viewBox="0 0 32 32" width="32" height="32"><path d="M10 16.5 L14.5 21 L22 12" stroke="#fff" stroke-width="2" fill="none" stroke-linecap="round" stroke-linejoin="round"/></svg></div>
    <div class="step-icon" style="top:175px"></div>
    <div class="step" style="top:36px"><h3>Challenge</h3><p>Sed ut perspiciatis unde omnis iste natus error sit voluptatem accusantium doloremque laudantium, totam rello inventecto beatae vitae dicta sunt explicabo.</p></div>
    <div class="step" style="top:104px"><h3>Solution</h3><p>Sed ut perspiciatis unde omnis iste natus error sit voluptatem accusantium doloremque laudantium, totam rello inventecto beatae vitae dicta sunt explicabo.</p></div>
    <div class="step" style="top:172px"><h3>Results</h3><p>Sed ut perspiciatis unde omnis iste natus error sit voluptatem accusantiumaudantium,</p></div>
    <svg class="footer" viewBox="0 0 431 22" fill="none" stroke="#fff" stroke-width=".8"><path d="M25 22 C25 10 31 2 45 2 H395 C404 2 406 10 409 22"/><path d="M404 22 C412 20 414 0 419 0 C424 0 425 20 431 22"/></svg>
    <div class="footer-text"><span class="ico"></span>Call Us : +1 555 014 2290 &nbsp;| &nbsp;<span class="ico"></span>info@velmoraquill.com</div>
    <div class="socials"><span></span><span></span><span></span></div>
    <div class="page-no">06</div>
  </section>

  <!-- About -->
  <section class="slide col-a row-3">
    <h2 class="slide-title">About <span class="accent">Us</span></h2>
    <div class="about-art" role="img" aria-label="Faint digital brand emblem built from data particles"></div>
    <div class="brand"><span class="brand-dot"></span>VELMORA QUILL INDUSTRIES</div>
    <p class="about-text body-text">Sed ut perspiciatis unde omnis iste natus error sit voluptatem accusantium doloremque laudantium, totam rem aperiam, eaque ipsa quae ab illo inventore veritatis et quasi architecto beatae vitae dicta sunt explicabo. Nemo enim ipsam voluptatem quia voluptas sit aspernatur aut odit aut fugit, sed quia consequuntur magni dolores eos qui ratione voluptatem sequi nesciunt. Neque porro quisquam est, qui dolorem ipsum quia dolor sit amet, consectetur, adipisci velit, sed quia non numquam eius modi tempora incidunt ut labore et dolore magnam aliquam quaerat voluptatem.</p>
    <div class="node-label" style="left:224px;top:49px">Lorem ipsum<br>dolorpsu</div>
    <div class="node" style="left:233px;top:67px"></div>
    <div class="node-label" style="left:262px;top:101px">Lorem ipsum<br>dolorpsu</div>
    <div class="node" style="left:311px;top:87px"></div>
    <div class="node" style="left:233px;top:165px"></div>
    <div class="node-label" style="left:224px;top:201px">Lorem ipsum<br>dolorpsu</div>
    <svg class="footer" viewBox="0 0 431 22" fill="none" stroke="#fff" stroke-width=".8"><path d="M25 22 C25 10 31 2 45 2 H395 C404 2 406 10 409 22"/><path d="M404 22 C412 20 414 0 419 0 C424 0 425 20 431 22"/></svg>
    <div class="footer-text"><span class="ico"></span>Call Us : +1 555 014 2290 &nbsp;| &nbsp;<span class="ico"></span>info@velmoraquill.com</div>
    <div class="socials"><span></span><span></span><span></span></div>
    <div class="page-no">03</div>
  </section>

  <!-- Team -->
  <section class="slide col-b row-3">
    <h2 class="slide-title">Our <span class="accent">Team</span></h2>
    <div class="brand"><span class="brand-dot"></span>VELMORA QUILL INDUSTRIES</div>
    <div class="member" style="left:36px"><div class="portrait" role="img" aria-label="Portrait photo of team member Arlen Voss"></div><h4>Arlen Voss</h4><p>Sed ut perspiciatis unde omnis iste natus error sit voluptatem accusantium doloremque laudantiutota rello inveno bdicta sunt explicabo.</p></div>
    <div class="member" style="left:167px"><div class="portrait" role="img" aria-label="Portrait photo of team member Mira Castell"></div><h4>Mira Castell</h4><p>Sed ut perspiciatis unde omnis iste natus error sit voluptatem accusantium doloremque laudantiutota rello inveno bdicta sunt explicabo.</p></div>
    <div class="member" style="left:298px"><div class="portrait" role="img" aria-label="Portrait photo of team member Dorian Pell"></div><h4>Dorian Pell</h4><p>Sed ut perspiciatis unde omnis iste natus error sit voluptatem accusantium doloremque laudantiutota rello inveno bdicta sunt explicabo.</p></div>
    <svg class="footer" viewBox="0 0 431 22" fill="none" stroke="#fff" stroke-width=".8"><path d="M25 22 C25 10 31 2 45 2 H395 C404 2 406 10 409 22"/><path d="M404 22 C412 20 414 0 419 0 C424 0 425 20 431 22"/></svg>
    <div class="footer-text"><span class="ico"></span>Call Us : +1 555 014 2290 &nbsp;| &nbsp;<span class="ico"></span>info@velmoraquill.com</div>
    <div class="socials"><span></span><span></span><span></span></div>
    <div class="page-no">07</div>
  </section>

  <!-- Section divider -->
  <section class="slide divider col-a row-4">
    <div class="divider-art" role="img" aria-label="Abstract burst of light data streams radiating from a dark sphere"></div>
    <div class="brand"><span class="brand-dot"></span>VELMORA QUILL INDUSTRIES</div>
    <div class="divider-band"></div>
    <h2 class="divider-title">SECTION DIVIDER</h2>
  </section>

  <!-- Thank you -->
  <section class="slide thanks col-b row-4">
    <div class="thanks-art" role="img" aria-label="Large translucent glowing brand emblem decoration"></div>
    <h2 class="slide-title">Thank <span class="accent">You</span></h2>
    <div class="brand"><span class="brand-dot"></span>VELMORA QUILL INDUSTRIES</div>
    <div class="contact">
      <h5>CONTACT INFO</h5>
      <p><span class="ico"></span>Call Us : +1 555 014 2290</p>
      <p><span class="ico"></span>info@velmoraquill.com</p>
      <div class="socials"><span></span><span></span><span></span></div>
    </div>
  </section>

</div>
</body>
</html>
```